Private Investigation Business Card Design

I need a business card for a new private investigation company named Brisk Inquiries. I perform mainly surveillance jobs, vehicle repossessions, document serves etc. The final design should aim for a professional look. The logo has a magnifying glass with stick man arms and legs and is in a running action to show the "Brisk" aspect of the name. If the colour scheme could remain the same as the website www.briskinquiries-demo.com.au with silvers,blacks and a couple electric blue highlights.
Industry/Entity Type
Business
Contact Information for Business Card
Morgan Kellaway
Brisk Inquiries
0487316204
PO Box 58, Carnwell NSW 2291
info@briskinquiries-demo.com.au
www.briskinquiries-demo.com.au
Look and feel

```html
<!DOCTYPE html>
<html lang="en">
<head>
<meta charset="utf-8">
<title>Brisk Inquiries – Business Card</title>
<link href="https://fonts.googleapis.com/css2?family=Arimo:wght@400;700&display=swap" rel="stylesheet">
<style>
  :root {
    --stage: #d4d4d4;
    --ink: #0f0f0f;
    --ink-soft: #2b2b2b;
    --paper-light: #ffffff;
    --paper-silver: #d6d6d6;
    --metal-light: #c9c9c9;
    --metal-dark: #7d7d7d;
    --text: #151515;
    --text-muted: #303030;
    --icon: #222222;
  }
  * { margin: 0; padding: 0; box-sizing: border-box; }
  html, body {
    width: 1200px;
    height: 871px;
    overflow: hidden;
    background: var(--stage);
    font-family: "Arimo", Arial, sans-serif;
  }
  .canvas {
    width: 1200px;
    height: 871px;
    display: flex;
    align-items: center;
    justify-content: center;
    gap: 40px;
  }
  .card {
    position: relative;
    width: 540px;
    height: 320px;
    overflow: hidden;
    box-shadow: 0 8px 24px rgba(0,0,0,0.25);
  }

  /* Back side */
  .card--back {
    background: linear-gradient(160deg, var(--metal-light) 0%, #a9a9a9 45%, var(--metal-dark) 100%);
  }
  .back__brand {
    position: absolute;
    left: 0;
    right: 0;
    top: 112px;
    display: flex;
    align-items: center;
    justify-content: center;
    gap: 12px;
  }
  .back__name {
    font-weight: 700;
    font-size: 34px;
    color: var(--ink);
  }
  .back__mark {
    width: 28px;
    height: 28px;
    border-radius: 50%;
    background: var(--ink);
  }
  .back__web {
    position: absolute;
    right: 40px;
    bottom: 40px;
    font-size: 15px;
    letter-spacing: 1.5px;
    color: var(--ink-soft);
  }

  /* Front side */
  .card--front {
    background: linear-gradient(160deg, var(--paper-light) 35%, var(--paper-silver) 100%);
  }
  .front__illustration {
    position: absolute;
    left: 0;
    top: 0;
    width: 215px;
    height: 100%;
    background: linear-gradient(135deg, var(--ink-soft) 0%, var(--ink) 70%);
  }
  .front__details {
    position: absolute;
    right: 26px;
    top: 52px;
    text-align: right;
    color: var(--text-muted);
  }
  .front__name {
    font-weight: 700;
    font-size: 19px;
    color: var(--text);
    margin-bottom: 20px;
  }
  .front__line {
    font-size: 13px;
    line-height: 17px;
  }
  .contact {
    list-style: none;
    margin-top: 2px;
  }
  .contact__item {
    display: flex;
    align-items: center;
    justify-content: flex-end;
    gap: 7px;
    font-size: 13px;
    line-height: 19px;
  }
  .contact__icon {
    width: 13px;
    height: 13px;
    fill: var(--icon);
    flex: none;
  }
  .front__brand {
    position: absolute;
    right: 26px;
    bottom: 30px;
    display: flex;
    align-items: center;
    gap: 10px;
  }
  .front__brand-name {
    font-weight: 700;
    font-size: 26px;
    color: var(--ink-soft);
  }
  .front__brand-mark {
    width: 22px;
    height: 22px;
    border-radius: 50%;
    background: var(--ink-soft);
  }
</style>
</head>
<body>
<main class="canvas">
  <section class="card card--back" aria-label="Card back">
    <div class="back__brand">
      <span class="back__name">Brisk Inquiries</span>
      <span class="back__mark" aria-hidden="true"></span>
    </div>
    <p class="back__web">www.briskinquiries-demo.com.au</p>
  </section>

  <section class="card card--front" aria-label="Card front">
    <div class="front__illustration" role="img" aria-label="Black panel with a large running figure and white speed lines"></div>

    <div class="front__details">
      <h1 class="front__name">Morgan Kellaway</h1>
      <p class="front__line">PO Box 58</p>
      <p class="front__line">Carnwell NSW 2291</p>
      <ul class="contact">
        <li class="contact__item">
          <span>0487 316 204</span>
          <svg class="contact__icon" viewBox="0 0 24 24" aria-hidden="true"><path d="M6.6 10.8a15.1 15.1 0 0 0 6.6 6.6l2.2-2.2a1 1 0 0 1 1-.25 11.4 11.4 0 0 0 3.6.57 1 1 0 0 1 1 1V20a1 1 0 0 1-1 1A17 17 0 0 1 3 4a1 1 0 0 1 1-1h3.5a1 1 0 0 1 1 1c0 1.25.2 2.45.57 3.6a1 1 0 0 1-.25 1z"/></svg>
        </li>
        <li class="contact__item">
          <span>info@briskinquiries-demo.com.au</span>
          <svg class="contact__icon" viewBox="0 0 24 24" aria-hidden="true"><path d="M2 5h20v14H2z M4 7v.4l8 5 8-5V7z" fill-rule="evenodd"/></svg>
        </li>
        <li class="contact__item">
          <span>www.briskinquiries-demo.com.au</span>
          <svg class="contact__icon" viewBox="0 0 24 24" aria-hidden="true"><circle cx="12" cy="12" r="10"/></svg>
        </li>
      </ul>
    </div>

    <div class="front__brand">
      <span class="front__brand-name">Brisk Inquiries</span>
      <span class="front__brand-mark" aria-hidden="true"></span>
    </div>
  </section>
</main>
</body>
</html>
```